Brindovalle Business cards

Dear team, I need to get the design file to suit it to our team. The focus of the business card is the Automotive Market and the design must be in black colour and the logo must be in glossy black. On the front of the card I need to get the following info:

- Name and Surname
- Title
- eMail
- Phone Number
- Skype account
- domain address

```html
<!DOCTYPE html>
<html lang="en">
<head>
<meta charset="utf-8">
<title>Brindovalle Business Cards</title>
<link href="https://fonts.googleapis.com/css2?family=Oswald:wght@600&family=Open+Sans:wght@400;600;700&display=swap" rel="stylesheet">
<style>
  :root {
    --stage: #3a3a3b;
    --stage-edge: #1f1f20;
    --card: #1b1b1d;
    --gloss: #2c2c2f;
    --accent: #e0262b;
    --ink-light: #f1f1f1;
    --ink-soft: #cfcfcf;
  }
  * { box-sizing: border-box; margin: 0; padding: 0; }
  html, body { width: 1200px; height: 900px; overflow: hidden; }
  body {
    background: radial-gradient(ellipse at 50% 45%, var(--stage) 0%, var(--stage-edge) 100%);
    font-family: "Open Sans", Arial, sans-serif;
    position: relative;
  }
  .card {
    position: absolute;
    top: 290px;
    width: 540px;
    height: 310px;
    background: var(--card);
    border-radius: 26px;
    box-shadow: 0 20px 40px rgba(0,0,0,0.45);
  }
  .card--brand { left: 40px; }
  .card--contact { left: 620px; }

  /* Brand side */
  .brand {
    position: absolute;
    left: 50%; top: 50%;
    transform: translate(-50%, -50%);
    display: flex;
    align-items: center;
    gap: 16px;
  }
  .brand__dot {
    width: 34px; height: 34px;
    border-radius: 50%;
    background: var(--accent);
  }
  .brand__name {
    font-weight: 700;
    font-size: 46px;
    letter-spacing: -0.5px;
    color: var(--gloss);
    font-family: "Open Sans", Arial, sans-serif;
  }

  /* Contact side */
  .person {
    position: absolute;
    right: 298px;
    top: 92px;
    text-align: right;
  }
  .person__name {
    font-family: "Oswald", "Arial Narrow", sans-serif;
    font-weight: 600;
    font-size: 32px;
    line-height: 1;
    color: var(--accent);
    text-transform: uppercase;
    letter-spacing: 0.5px;
  }
  .person__title {
    margin-top: 6px;
    font-size: 14px;
    color: var(--ink-soft);
  }
  .divider {
    position: absolute;
    left: 258px;
    top: 100px;
    width: 2px;
    height: 64px;
    background: var(--accent);
  }
  .contacts {
    position: absolute;
    left: 276px;
    top: 96px;
    list-style: none;
  }
  .contacts li {
    display: flex;
    align-items: center;
    gap: 7px;
    font-size: 14px;
    line-height: 24px;
    color: var(--ink-light);
  }
  .contacts svg { width: 11px; height: 11px; flex: none; }
  .address {
    position: absolute;
    left: 0; right: 0;
    top: 214px;
    text-align: center;
    font-size: 14px;
    color: var(--ink-light);
  }
</style>
</head>
<body>
  <section class="card card--brand">
    <div class="brand">
      <span class="brand__dot"></span>
      <span class="brand__name">Brindovalle.com</span>
    </div>
  </section>

  <section class="card card--contact">
    <div class="person">
      <h1 class="person__name">Marlo Venturi</h1>
      <p class="person__title">Director</p>
    </div>
    <span class="divider"></span>
    <ul class="contacts">
      <li>
        <svg viewBox="0 0 12 12" aria-hidden="true"><path d="M3 1 L5 3.5 L4 5 Q5 7 7 8 L8.5 7 L11 9 L9.5 11 Q5 11 1 3 Z" fill="#e0262b"/></svg>
        555-014-2287
      </li>
      <li>
        <svg viewBox="0 0 12 12" aria-hidden="true"><rect x="0.5" y="2" width="11" height="8" fill="#e0262b"/><path d="M0.5 2 L6 6.5 L11.5 2" fill="none" stroke="#1b1b1d" stroke-width="1"/></svg>
        info@brindovalle.com
      </li>
      <li>
        <svg viewBox="0 0 12 12" aria-hidden="true"><circle cx="6" cy="6" r="5.5" fill="#e0262b"/></svg>
        brindovalle
      </li>
    </ul>
    <p class="address">1820 W Corvine Ave, Larkfield, Ohio 44017</p>
  </section>
</body>
</html>
```